Bifold brochure design for leadership academy

Please see below. This is a bifold brochure for a leadership academy. (www.brv.institute). Look and feel must be colours, shapes, abstract designs, graphics, pictures. Make this professional, yet casual and bold.

Feel free to design just the front and back cover, then I'll give feedback on whether or not you're in the right direction.

COVER
- Title: “The Boldest Bridge Year Journey”
- “Northward Mentor Institute” logo somewhere
- Subtitles (with images, icons, and/or shapes): “Self-discovery” “Skills development” “Real-world Impact”

PAGE 2 (Inside Fold)
- Title: "The Program"
- Section 2a: Section title: "How it works”
- Image: See website, image under "four phases of the program". Please adapt and make it look better
- Text: NMI is a structured, 8-month ‘gap year’ program for 18-25 year olds who want more than just a year off – they want a year ahead. Our aim is to develop high-potential young leaders with strong values, clear purpose, high-impact skills, and a track record of real-world accomplishments that are second-to-none. We do this through four-phases.
- Section 2b: Section title: “Dates & Timing”
- Image: See image on website under 'dates and timing'. Make sure both dates show up on the brochure (September and January program).
- Text: There are two programs per year: one that starts in September, the other in January. The first four months of the program are based in Toronto at the NMI headquarters. The curriculum we work through is highly engaging and personalized, focusing directly on students’ goals. After that, students are out in the world, achieving the remaining components of the program (e.g. internship, volunteer abroad).

PAGE 3 (Outside Fold)
- Page Title: "The Students"
- Section 3a: Section title: “Who’s it for”
- Subtitle1: “High school graduates”
 Image/icon of a high school grad
 Text1: 90% of high school grads aren't sure why they’re going to university or what they want to study.
 Text2: NMI helps students discover what they truly want to do in life, and make enormous progress towards these goals.

- Subtitle2: “Post-secondary students”
 Image/icon of a university / college student
 Text1: 28% of students switch or drop out of their program because it wasn’t for them or they didn’t like it.
 Text2: Don't keep moving around or risk switching careers down the road – find out what sparks your passion with NMI.

- Subtitle3: “Post-secondary graduates”
 Image/icon of a university/ college grad
 Text1: 50% of graduates are unemployed or underemployed, 60% are in debt.
 Text2: NMI will help you get your dream job – our students won’t settle for anything less.

- Section 3b: Section title: “How to apply”
 Text1: We select high-potential young leaders with a desire to improve themselves and impact the world.
 Text2: We won’t ask you for your grades – we care more about your values and potential.
 Text3: Visit www.brv.institute to apply now

BACK COVER
- Page Title: “Get in Touch”
- Website: www.brv.institute
- Facebook page: facebook.com/brv.institute
- Twitter handle: @brv_institute
- Email: tomas@brv.institute

Project Deadline Extended Reason: Made a mistake initially only giving designers 2 days to submit. This allows for more high quality designs. Thank you. Added Wednesday, March 18, 2015

Target Market(s)

18-25 year olds, parents, teachers

Industry/Entity Type

Leadership

Requirements
Must have
• Beautiful design - sleek and bold, yet colourful and casual. Keep the colours similar to our website (www.brv.institute). See examples of other brochures.
• http://img.pelvoro.net/jpg/00/11/22/33/240_F_11223344_xQr8LmPzTw3KdNvBsYcHuJeFa2gkTqWn.jpg
• http://vantoliq.com/wp-content/uploads/2014/11/Real-Estate-Bi-fold-Brochure.jpg
• http://www.murablo.com/media/k2/galleries/5/001-bi-fold-brochure-psd-mock-up-template.jpg
• http://img.pelvoro.net/jpg/00/44/55/66/240_F_44556677_Zk3wPqLm8RtYvBnXcDs2HjKuE5fa9Gq0.jpg

```html
<!DOCTYPE html>
<html lang="en">
<head>
<meta charset="utf-8">
<title>Northward Mentor Institute – Brochure Spread</title>
<link href="https://fonts.googleapis.com/css2?family=Montserrat:ital,wght@0,400;0,500;0,700;0,800;1,400&display=swap" rel="stylesheet">
<style>
:root{
  --backdrop:#e9e9e9;
  --paper:#efe4c6;
  --paper-dark:#e4d5ab;
  --blue:#2f6aa8;
  --red:#c4283a;
  --gold:#e9b52c;
  --yellow:#f3d63a;
  --mustard:#dca62a;
  --green:#c9d97e;
  --cal-a:#f2e07a;
  --cal-b:#e8cb52;
  --cal-head:#f1c93a;
  --ink:#3b3528;
  --photo-warm:#c9a58a;
  --photo-cool:#9fb0bf;
}
*{box-sizing:border-box;margin:0;padding:0}
html,body{width:1200px;height:800px;overflow:hidden}
body{background:var(--backdrop);font-family:"Montserrat",Arial,sans-serif;color:var(--ink);position:relative}
.spread{position:absolute;left:50px;top:60px;width:1100px;height:680px;box-shadow:0 12px 30px rgba(0,0,0,.18)}
.page{position:absolute;top:0;width:550px;height:680px;background:var(--paper);overflow:hidden}
.page--left{left:0}
.page--right{left:550px}
.fold{position:absolute;left:548px;top:0;width:4px;height:680px;background:linear-gradient(90deg,rgba(0,0,0,.08),rgba(0,0,0,0));z-index:5}
.abs{position:absolute}
.photo{position:absolute;background:linear-gradient(135deg,var(--photo-warm),var(--photo-cool))}

/* Left page */
.tab{background:var(--blue);color:#fff;font-weight:800;text-transform:uppercase;letter-spacing:.5px;white-space:nowrap}
.program-tab{left:0;top:40px;width:260px;height:54px;font-size:28px;line-height:54px;padding-left:22px}
.program-photo{left:0;top:110px;width:260px;height:270px}
.how-it-works{left:282px;top:56px;width:245px}
.section-heading{font-weight:800;font-size:15px;text-transform:uppercase;letter-spacing:.4px;margin-bottom:8px}
.body-copy{font-size:12px;line-height:1.5}
.phases{left:0;top:400px;width:550px;height:280px;display:flex}
.phase{position:relative;flex:1;padding:70px 16px 16px}
.phase--design{background:var(--gold)}
.phase--build{background:var(--yellow)}
.phase--achieve{background:var(--mustard)}
.ribbon{position:absolute;left:0;top:22px;background:var(--red);color:#fff;font-weight:700;font-size:17px;padding:6px 22px 6px 14px;clip-path:polygon(0 0,100% 0,88% 50%,100% 100%,0 100%)}
.phase-icon{position:absolute;right:18px;top:14px}
.phase ol{padding-left:16px;margin-top:4px}

/* Right page */
.dates{left:22px;top:30px;width:214px}
.dates .body-copy{font-size:10.5px;line-height:1.45}
.calendar{left:240px;top:22px;width:296px;height:196px;display:grid;grid-template-columns:56px repeat(12,1fr);grid-template-rows:22px 1fr 1fr}
.cal-head{background:var(--cal-head);font-size:7px;font-weight:700;text-align:center;line-height:22px}
.cal-corner{background:var(--paper-dark)}
.cal-cell:nth-child(odd){background:var(--cal-a)}
.cal-cell:nth-child(even){background:var(--cal-b)}
.cal-label{background:var(--paper-dark);display:flex;flex-direction:column;align-items:center;justify-content:center;gap:4px;font-size:9px;font-weight:800;color:var(--blue)}
.cal-label .thumb{width:44px;height:30px;background:linear-gradient(135deg,var(--photo-warm),var(--photo-cool))}
.brand-mark{display:flex;align-items:center;gap:3px}
.brand-mark i{display:block;width:7px;height:7px;background:var(--blue)}
.event{position:relative;z-index:2;align-self:start;justify-self:start;padding-left:2px;font-size:6px;line-height:1.2;white-space:nowrap;display:flex;align-items:center;gap:2px}
.event::before{content:"";width:5px;height:5px;border-radius:50%;background:var(--red);flex:none}

.students-bg{left:0;top:230px}
.students-tab{left:18px;top:330px;width:50px;height:210px;display:flex;align-items:center;justify-content:center}
.students-tab span{transform:rotate(-90deg);white-space:nowrap;font-size:24px}
.whos-for{left:230px;top:272px;font-weight:800;font-size:13px}
.audience{position:absolute;top:298px;width:145px}
.audience--hs{left:80px}
.audience--ps{left:238px}
.audience--grad{left:396px}
.audience .photo{position:relative;width:145px;height:96px}
.audience h3{color:var(--red);font-weight:800;font-size:12px;text-transform:uppercase;line-height:1.2;margin:10px 0 8px}
.stat{display:flex;gap:7px;align-items:flex-start;margin-bottom:10px}
.stat-box{flex:none;background:var(--red);color:#fff;font-weight:500;font-size:24px;width:58px;height:50px;display:flex;align-items:center;justify-content:center}
.stat p{font-size:10.5px;line-height:1.35}
.pitch{font-size:10.5px;line-height:1.45;font-style:italic}
</style>
</head>
<body>
<div class="spread">
  <section class="page page--left">
    <div class="abs tab program-tab">The Program</div>
    <div class="photo program-photo" role="img" aria-label="Photo of smiling young students"></div>
    <div class="abs how-it-works">
      <h2 class="section-heading">How it works</h2>
      <p class="body-copy">NMI is a structured, 8-month ‘gap year’ program for 18-25 year olds who want more than just a year off – they want a year ahead. Our aim is to develop high-potential young leaders with strong values, clear purpose, high-impact skills, and a track record of real-world accomplishments that are second-to-none. We do this through four-phases.</p>
    </div>
    <div class="abs phases">
      <div class="phase phase--design">
        <span class="ribbon">Design</span>
        <svg class="phase-icon" width="34" height="38" viewBox="0 0 34 38"><rect x="3" y="3" width="28" height="32" fill="#fff" stroke="#222" stroke-width="3"/><rect x="9" y="11" width="16" height="3" fill="#222"/><rect x="9" y="18" width="16" height="3" fill="#222"/><rect x="9" y="25" width="10" height="3" fill="#222"/></svg>
        <p class="body-copy">Design your year in the program and learn how to manage goals through our advanced goal-setting training.</p>
      </div>
      <div class="phase phase--build">
        <span class="ribbon">Build</span>
        <svg class="phase-icon" width="40" height="34" viewBox="0 0 40 34"><rect x="14" y="10" width="12" height="24" fill="#222"/><rect x="2" y="18" width="12" height="16" fill="#222"/><rect x="26" y="22" width="12" height="12" fill="#222"/></svg>
        <p class="body-copy">Build a set of skills that will directly help you achieve your goals, including issue-based problem solving, creativity, and structured communications.</p>
      </div>
      <div class="phase phase--achieve">
        <span class="ribbon">Achieve</span>
        <svg class="phase-icon" width="40" height="30" viewBox="0 0 40 30"><rect x="2" y="10" width="8" height="20" fill="#222"/><rect x="16" y="4" width="8" height="26" fill="#222"/><rect x="30" y="10" width="8" height="20" fill="#222"/></svg>
        <p class="body-copy">Achieve six things before you can graduate:</p>
        <ol class="body-copy">
          <li>Solve a social problem</li>
          <li>Conquer a physical feat</li>
          <li>Organize an event</li>
          <li>Volunteer abroad</li>
          <li>Start something</li>
          <li>Do an internship</li>
        </ol>
      </div>
    </div>
  </section>

  <div class="fold"></div>

  <section class="page page--right">
    <div class="abs dates">
      <h2 class="section-heading">Dates &amp; Timing</h2>
      <p class="body-copy">There are two programs per year: one that starts in September, the other in January. The first four months of the program are based in Toronto at the NMI headquarters. The curriculum we work through is highly engaging and personalized, focusing directly on students’ goals. After that, students are out in the world, achieving the remaining components of the program (e.g. internship, volunteer abroad).</p>
    </div>

    <div class="abs calendar">
      <div class="cal-head cal-corner"></div>
      <div class="cal-head">AUG</div><div class="cal-head">SEP</div><div class="cal-head">OCT</div><div class="cal-head">NOV</div><div class="cal-head">DEC</div><div class="cal-head">JAN</div><div class="cal-head">FEB</div><div class="cal-head">MAR</div><div class="cal-head">APR</div><div class="cal-head">MAY</div><div class="cal-head">JUN</div><div class="cal-head">JUL</div>

      <div class="cal-label"><div class="thumb" role="img" aria-label="Photo of September students"></div><span class="brand-mark"><i></i>NMI</span></div>
      <div class="cal-cell"></div><div class="cal-cell"></div><div class="cal-cell"></div><div class="cal-cell"></div><div class="cal-cell"></div><div class="cal-cell"></div><div class="cal-cell"></div><div class="cal-cell"></div><div class="cal-cell"></div><div class="cal-cell"></div><div class="cal-cell"></div><div class="cal-cell"></div>

      <div class="cal-label"><div class="thumb" role="img" aria-label="Photo of January students"></div><span class="brand-mark"><i></i>NMI</span></div>
      <div class="cal-cell"></div><div class="cal-cell"></div><div class="cal-cell"></div><div class="cal-cell"></div><div class="cal-cell"></div><div class="cal-cell"></div><div class="cal-cell"></div><div class="cal-cell"></div><div class="cal-cell"></div><div class="cal-cell"></div><div class="cal-cell"></div><div class="cal-cell"></div>

      <span class="event" style="grid-row:2;grid-column:3 / span 3;margin-top:8px">Begin design</span>
      <span class="event" style="grid-row:2;grid-column:3 / span 3;margin-top:30px">Build skills</span>
      <span class="event" style="grid-row:2;grid-column:6 / span 2;margin-top:52px">Set goals</span>
      <span class="event" style="grid-row:2;grid-column:7 / span 2;margin-top:8px">Achieve</span>
      <span class="event" style="grid-row:2;grid-column:10 / span 2;margin-top:30px">Volunteer</span>
      <span class="event" style="grid-row:2;grid-column:11 / span 3;margin-top:52px">Internship</span>

      <span class="event" style="grid-row:3;grid-column:7 / span 3;margin-top:8px">Begin design</span>
      <span class="event" style="grid-row:3;grid-column:7 / span 3;margin-top:30px">Build skills</span>
      <span class="event" style="grid-row:3;grid-column:10 / span 2;margin-top:8px">Achieve</span>
      <span class="event" style="grid-row:3;grid-column:11 / span 2;margin-top:30px">Volunteer</span>
      <span class="event" style="grid-row:3;grid-column:12 / span 2;margin-top:52px">Start</span>
      <span class="event" style="grid-row:3;grid-column:12 / span 2;margin-top:8px">Internship</span>
    </div>

    <svg class="abs students-bg" width="550" height="450" viewBox="0 0 550 450" aria-hidden="true">
      <path d="M0 40 C150 10 380 10 550 0 L550 450 L0 450 Z" fill="#c9d97e"/>
    </svg>

    <div class="abs tab students-tab"><span>The Students</span></div>
    <div class="abs whos-for">WHO’S IT FOR</div>

    <div class="audience audience--hs">
      <div class="photo" role="img" aria-label="Photo of high school graduates"></div>
      <h3>High school graduates</h3>
      <div class="stat"><div class="stat-box">90%</div><p>of high school grads aren’t sure why they’re going to university or what they want to study.</p></div>
      <p class="pitch">NMI helps students discover what they truly want to do in life, and make enormous progress towards these goals.</p>
    </div>

    <div class="audience audience--ps">
      <div class="photo" role="img" aria-label="Photo of a group of college students"></div>
      <h3>Post-secondary students</h3>
      <div class="stat"><div class="stat-box">28%</div><p>of students switch or drop out of their program because it wasn’t for them or they didn’t like it.</p></div>
      <p class="pitch">Don’t keep moving around or risk switching careers down the road – find out what sparks your passion with NMI.</p>
    </div>

    <div class="audience audience--grad">
      <div class="photo" role="img" aria-label="Photo of university graduates celebrating"></div>
      <h3>Post-secondary graduates</h3>
      <div class="stat"><div class="stat-box">50%</div><p>of graduates are unemployed or underemployed, 60% are in debt.</p></div>
      <p class="pitch">NMI will help you get your dream job – our students won’t settle for anything less.</p>
    </div>
  </section>
</div>
</body>
</html>
```